Online Advertising: What gets us excited?

We need a poster that helps make it obvious who we are as a software delivery team.

Background: Our company's culture thrives on "ideas". We use those ideas from every member of our team to innovate and beat out the competition. We hire the kind of people that are bursting with ideas and just need a place to put them into practice.

Design Brief: In this poster design, I imagine a cross between those standard "inspirational posters", like http://qvx.example/t7mWpa

a funny cartoon, like a Odd Porch comic http://qvx.example/k4hNbd

and an TJ Rolwand morphing of shapes. http://qvx.example/w2yPuf

The picture should embody this: A computer programmer wrapped in ideas as an artist painting systems onto a canvas. The canvas sits on an easel that represents our suite of web advertising products. And the artist works amongst others in the Brindle Works art studio, which represents our company headquarters.

The tagline might read:
"Brindle Works products are the canvas where I paint my ideas!"

I am not disclosing the name of the company, so feel free to use "Brindle Works". Feel free to ask any questions you like.

For the winning design, I will likely followup with additional adjustments and variations on this theme.

Reason: 5 days was not enough time for all of us. I did not provide feedback quickly enough for you to hone your designs. Please do continue to develop your ideas a bit, based on my feedback.

Reason: Allow for more designs. None of the images are exactly hitting that right sense of creativity and software creation, being combined.

Target Market(s)

Our employees, especially our engineering team of programmers, testers, web designers, project managers, and product managers.

Industry/Entity Type

Software

Font styles to use
Sans Serif

Requirements
Must have
• Immediate appeal. Easy to understand at a glance, yet nuanced deeper meaning.
Nice to have
• Fine details that intrigue people.
Should not have
• Gender bias - must support men and women. Racial bias - must not exclude any races.

```html
<!DOCTYPE html>
<html lang="en">
<head>
<meta charset="utf-8">
<title>The Canvas – Brindle Works products</title>
<link rel="stylesheet" href="https://fonts.googleapis.com/css2?family=Special+Elite&family=Playfair+Display:ital,wght@1,900&display=swap">
<style>
  :root {
    --ink: #111111;
    --paint-red: #d8432c;
    --paint-orange: #ea8a2e;
    --paint-yellow: #e6d84c;
    --paint-lime: #a8c944;
    --paint-green: #3aa85a;
    --paint-deep-green: #2f8f4e;
    --wood: #5b2f24;
    --wood-dark: #3c1f1a;
    --desk-silver: #d9d9dc;
    --charcoal: #555555;
  }
  html, body {
    margin: 0;
    padding: 0;
    width: 1200px;
    height: 805px;
    overflow: hidden;
    background: #ffffff;
  }
  .poster {
    position: relative;
    width: 1200px;
    height: 805px;
    overflow: hidden;
  }
  .studio-scene {
    position: absolute;
    inset: 0;
    background:
      radial-gradient(ellipse 220px 170px at 1090px 150px, var(--wood-dark) 0%, rgba(60,31,26,0) 100%),
      radial-gradient(ellipse 180px 140px at 640px 250px, var(--wood) 0%, rgba(91,47,36,0) 100%),
      radial-gradient(ellipse 300px 220px at 1010px 720px, var(--wood) 0%, rgba(91,47,36,0) 100%),
      radial-gradient(ellipse 260px 200px at 110px 710px, var(--charcoal) 0%, rgba(85,85,85,0) 100%),
      radial-gradient(ellipse 200px 140px at 250px 120px, var(--desk-silver) 0%, rgba(217,217,220,0) 100%),
      radial-gradient(ellipse 340px 200px at 500px 540px, var(--desk-silver) 0%, rgba(217,217,220,0) 100%),
      linear-gradient(180deg,
        var(--paint-red) 0%,
        var(--paint-orange) 17%,
        var(--paint-yellow) 37%,
        var(--paint-lime) 56%,
        var(--paint-green) 78%,
        var(--paint-deep-green) 100%);
  }
  .type-layer {
    position: absolute;
    inset: 0;
    width: 1200px;
    height: 805px;
  }
  .brand-line,
  .tagline {
    font-family: "Special Elite", "Courier New", monospace;
    font-weight: 400;
    fill: var(--ink);
  }
  .brand-line { font-size: 46px; }
  .tagline { font-size: 82px; }
  .headline {
    font-family: "Playfair Display", Georgia, serif;
    font-style: italic;
    font-weight: 900;
    fill: var(--ink);
  }
  .headline-small { font-size: 62px; }
  .headline-large { font-size: 124px; }
</style>
</head>
<body>
  <main class="poster">
    <div class="studio-scene" role="img" aria-label="A programmer's desk with monitor, keyboard and calendar tablet, painted over as an artist's canvas with broad brush strokes in red, orange, yellow, green, grey and brown"></div>
    <svg class="type-layer" viewBox="0 0 1200 805" aria-labelledby="poster-title">
      <defs>
        <filter id="headline-shadow" x="-10%" y="-20%" width="130%" height="150%">
          <feDropShadow dx="4" dy="5" stdDeviation="3" flood-color="#3c3c3c" flood-opacity="0.55"/>
        </filter>
      </defs>
      <text class="brand-line" x="60" y="95" textLength="490" lengthAdjust="spacingAndGlyphs">Brindle Works products</text>
      <text id="poster-title" class="headline" filter="url(#headline-shadow)">
        <tspan class="headline-small" x="258" y="400" textLength="94" lengthAdjust="spacingAndGlyphs">The</tspan>
        <tspan class="headline-large" x="462" y="402" textLength="474" lengthAdjust="spacingAndGlyphs">Canvas</tspan>
      </text>
      <text class="tagline" x="100" y="535" textLength="1020" lengthAdjust="spacingAndGlyphs">where I paint my ideas!</text>
    </svg>
  </main>
</body>
</html>
```